Lurvik.no is a new website about pedagogical entrepreneurship. It's main target group is teachers. The Nordic Bureau for Digital Schooling and the National Office for Learning and Classrooms are leading the project.

The web page is meant to show examples of how different methods of entrepreneurship can be used pedagogical in a learning environment. The page will also support the user with examples of different teaching programs and other examples of best practice.

Pedagogical entrepreneurship is not about business and men in suits. It's a method for learning. The focus in the design should be on school, education and new ways of learning.

The final product should be motivating and engaging, but at the same time governmental and serious. We are not looking for something "flashy" and corporate-looking, but a moderate, task-focused and clean design that state quality.

We need designs for three pages:
1 - frontpage
2 - subpage ("Metoder og undervisningsopplegg")
3 - subpage ("Små-TOPP i Vassbygd")

The interaction design for these three pages will be uploaded as an attachment.

We would like you to find inspiration in the following websites:
- www.skapekraft.no
- www.giellu.no
- www.brightfernlab.com
- www.zyx.no
(more will be added)

Please use the attached logo, and feel free to use this as an inspiration for the rest of the design.

Target Market(s)

Teachers

Industry/Entity Type

Education

Requirements
Must have
• * Header with: Logo. Main navigation. Utility navigation. Search box.
* Footer
Should not have
• Images of men in suits.
Very strong graphical elements that stands out too much (we want it clean).

```html
<!DOCTYPE html>
<html lang="en">
<head>
<meta charset="utf-8">
<title>Lurvik.no – Pedagogical Entrepreneurship</title>
<link rel="stylesheet" href="https://fonts.googleapis.com/css2?family=Open+Sans:wght@400;600&family=Oswald:wght@400;500&family=Arimo:wght@400;700&display=swap">
<style>
  :root {
    --navy: #0a1f40;
    --sky: #0e94d6;
    --nav-link: #8fd4f7;
    --card-light: #4cbbec;
    --card-mid: #1aa3e2;
    --card-dark: #0b6ea9;
    --card-edge: #0d5f95;
    --bar-light: #5ec6ef;
    --bar-dark: #0a6aa5;
    --ink: #222;
    --heading-blue: #1b8fc8;
    --footer-bg: #343434;
    --footer-text: #cfcfcf;
    --footer-head: #e6e6e6;
    --pill: #cfcfcf;
  }
  * { box-sizing: border-box; margin: 0; padding: 0; }
  html, body { width: 1000px; height: 1200px; overflow: hidden; }
  body { position: relative; background: #fff; font-family: "Open Sans", sans-serif; color: var(--ink); }
  .abs { position: absolute; }

  /* Header */
  .header { left: 0; top: 0; width: 1000px; height: 480px;
    background: linear-gradient(180deg, var(--navy) 0%, #0c3a6e 35%, #0c73b6 70%, var(--sky) 100%); }
  .utility-nav { right: 62px; top: 31px; font-size: 14px; color: var(--nav-link); }
  .utility-nav span.sep { margin: 0 12px; }
  .brand { left: 24px; top: 58px; display: flex; align-items: center; gap: 14px; }
  .brand-mark { width: 56px; height: 56px; border-radius: 50%; background: #d7e6f2; }
  .brand-name { font-family: "Arimo", sans-serif; font-weight: 700; font-size: 50px; line-height: 50px; color: #9fd3f3; }
  .brand-tag { left: 123px; top: 114px; font-family: "Arimo", sans-serif; font-size: 11px; color: #dde8f2; }
  .search { left: 640px; top: 82px; width: 270px; height: 31px; background: #edf0f3; border: 1px solid #c7d0d9;
    font-style: italic; font-size: 13px; color: #7a8794; padding: 6px 12px; }
  .search-btn { left: 913px; top: 85px; width: 28px; height: 28px; }

  .card { width: 292px; height: 258px; }
  .card svg { position: absolute; left: 0; top: 0; }
  .card-title { position: absolute; left: 0; top: 10px; width: 220px; text-align: center;
    font-family: "Oswald", sans-serif; font-size: 26px; line-height: 36px; color: #fff; }
  .card-body { position: absolute; left: 18px; top: 96px; width: 208px; font-size: 11px; line-height: 15.5px;
    text-align: justify; color: #10283e; }
  .card-more { position: absolute; left: 124px; top: 218px; font-size: 11px; color: #10283e; display: flex; align-items: center; gap: 6px; }
  .card-more i { width: 14px; height: 14px; border-radius: 50%; background: #eef2f5; border: 1px solid #9aa; display: inline-flex; align-items: center; justify-content: center; }
  .card-more i::after { content: ""; border-left: 5px solid #555; border-top: 3px solid transparent; border-bottom: 3px solid transparent; margin-left: 1px; }

  /* Meter */
  .meter { left: 23px; top: 507px; width: 276px; height: 259px; border: 1px solid #d6d6d6;
    background: linear-gradient(180deg, #ffffff 0%, #e9e9e9 70%, #d9d9d9 100%); }
  .meter svg { position: absolute; left: 0; top: 0; }
  .meter-q { position: absolute; left: 0; top: 16px; width: 100%; text-align: center; font-family: "Arimo", sans-serif; font-size: 15px; }
  .meter-check { position: absolute; left: 0; top: 204px; width: 100%; text-align: center; font-family: "Arimo", sans-serif; font-size: 14px; }
  .meter-try { position: absolute; left: 0; top: 222px; width: 100%; text-align: center; font-family: "Arimo", sans-serif;
    font-size: 20px; color: var(--heading-blue); text-decoration: underline; }

  /* Section bars */
  .bar { height: 38px; border-radius: 6px; display: flex; align-items: center; gap: 10px; padding-left: 9px;
    font-family: "Oswald", sans-serif; font-size: 18px; color: #fff; }
  .bar i { width: 16px; height: 16px; border-radius: 50%; background: #fff; display: inline-flex; align-items: center; justify-content: center; }
  .bar i::after { content: ""; border-left: 5px solid #555; border-top: 3px solid transparent; border-bottom: 3px solid transparent; margin-left: 1px; }
  .bar-start { left: 319px; top: 507px; width: 652px; background: var(--bar-light); }
  .bar-inspire { left: 24px; top: 784px; width: 948px; background: var(--bar-dark); }

  .start-box { left: 319px; top: 552px; width: 652px; height: 214px; border: 1px solid #d2d2d2; }
  .col { position: absolute; top: 14px; width: 200px; }
  .col h3 { font-family: "Arimo", sans-serif; font-weight: 400; font-size: 15px; color: var(--heading-blue); margin-bottom: 9px; }
  .col h3.plain { color: #222; }
  .col li { list-style: none; font-family: "Arimo", sans-serif; font-size: 12px; line-height: 30px; padding-left: 24px; position: relative; }
  .col li::before { content: "⇢"; position: absolute; left: 4px; font-size: 9px; }
  .divider { position: absolute; top: 50px; width: 1px; height: 110px; background: linear-gradient(180deg, transparent, #333, transparent); }
  .pill-dark { position: absolute; top: 180px; width: 66px; height: 21px; border-radius: 11px; background: #2d2d2d; color: #fff;
    font-family: "Oswald", sans-serif; font-size: 11px; display: flex; align-items: center; justify-content: center; gap: 4px; }

  /* Inspiration */
  .thumb { top: 843px; width: 179px; height: 121px; border: 1px solid #666; }
  .thumb .photo { width: 100%; height: 100%; }
  .thumb .label { position: absolute; left: 0; bottom: 0; width: 100%; height: 26px; background: rgba(0,0,0,.55);
    color: #fff; font-family: "Arimo", sans-serif; font-size: 12px; display: flex; align-items: center; justify-content: center; }
  .photo-a { background: linear-gradient(180deg, #c9d2d8 0%, #8d8f8a 45%, #6e5a4f 75%, #5b5650 100%); }
  .photo-b { background: linear-gradient(180deg, #b2b8bf 0%, #8a7266 40%, #7d8a6b 80%, #5c5c52 100%); }
  .photo-c { background: linear-gradient(180deg, #4a86d0 0%, #b8c6cf 45%, #e3842c 60%, #6f8a54 100%); }
  .slide-arrow { top: 892px; width: 0; height: 0; border-top: 13px solid transparent; border-bottom: 13px solid transparent; }

  /* Footer */
  .footer { left: 0; top: 983px; width: 1000px; height: 217px; background: var(--footer-bg); }
  .fcol { position: absolute; top: 34px; }
  .fcol h4 { font-family: "Oswald", sans-serif; font-weight: 400; font-size: 14px; color: var(--footer-head); margin-bottom: 15px; }
  .fcol p { font-size: 12px; line-height: 16.8px; color: var(--footer-text); }
  .pill { position: absolute; width: 66px; height: 21px; border-radius: 11px; background: var(--pill); color: #333;
    font-family: "Oswald", sans-serif; font-size: 11px; display: flex; align-items: center; justify-content: center; }
  .f-divider { left: 780px; top: 30px; width: 1px; height: 115px; background: #555; }
  .social { top: 29px; width: 33px; height: 33px; border-radius: 4px; background: #8a8a8a; }
  .f-mark { left: 861px; top: 86px; width: 62px; height: 62px; border-radius: 50%; background: #c9c9c9; }
  .f-copy { left: 780px; top: 176px; width: 220px; text-align: center; font-size: 11px; line-height: 16px; color: var(--footer-text); }
</style>
</head>
<body>

<header class="abs header">
  <nav class="abs utility-nav">Best Practice Schools<span class="sep">|</span>Lurvikmeter<span class="sep">|</span>About Lurvik.no</nav>
  <div class="abs brand"><span class="brand-mark"></span><span class="brand-name">Lurvik</span></div>
  <div class="abs brand-tag">Entreprenørielle metoder i undervisningen</div>
  <div class="abs search">Search Here</div>
  <svg class="abs search-btn" viewBox="0 0 28 28">
    <circle cx="14" cy="14" r="13" fill="#eef1f4" stroke="#9aa6b1"/>
    <circle cx="12.5" cy="12.5" r="4.5" fill="none" stroke="#333" stroke-width="2"/>
    <line x1="16" y1="16" x2="20" y2="20" stroke="#333" stroke-width="2.5" stroke-linecap="round"/>
  </svg>

  <article class="abs card" style="left:70px;top:175px">
    <svg width="292" height="258" viewBox="0 0 292 258"><polygon points="3,3 216,3 289,128 216,255 3,255" fill="var(--card-light)" stroke="#2c9bd4" stroke-width="3" stroke-linejoin="round"/></svg>
    <h2 class="card-title" style="font-weight:400">What is Pedagogical<br>Entrepreneurship ?</h2>
    <p class="card-body">Lorem ipsum dolor sit amet, consectetur adipisicing elit, sed do eiusmod tempor incididunt ut labore et dolore magna aliqua. Ut enim ad minim veniam, quis nostrud exercitation ullamco laboris nisi ut aliquip ex ea commodo consequat.</p>
    <span class="card-more">READ MORE <i></i></span>
  </article>
  <article class="abs card" style="left:370px;top:175px">
    <svg width="292" height="258" viewBox="0 0 292 258"><polygon points="3,3 216,3 289,128 216,255 3,255" fill="var(--card-mid)" stroke="#1387c4" stroke-width="3" stroke-linejoin="round"/></svg>
    <h2 class="card-title" style="font-weight:400">Methods &amp; Teaching<br>Plans</h2>
    <p class="card-body">Lorem ipsum dolor sit amet, consectetur adipisicing elit, sed do eiusmod tempor incididunt ut labore et dolore magna aliqua. Ut enim ad minim veniam, quis nostrud exercitation ullamco laboris nisi ut aliquip ex ea commodo consequat.</p>
    <span class="card-more">READ MORE <i></i></span>
  </article>
  <article class="abs card" style="left:670px;top:175px">
    <svg width="292" height="258" viewBox="0 0 292 258"><polygon points="3,3 216,3 289,128 216,255 3,255" fill="var(--card-dark)" stroke="var(--card-edge)" stroke-width="3" stroke-linejoin="round"/></svg>
    <h2 class="card-title" style="font-weight:400">Good Examples /<br>Best Practices</h2>
    <p class="card-body">Lorem ipsum dolor sit amet, consectetur adipisicing elit, sed do eiusmod tempor incididunt ut labore et dolore magna aliqua. Ut enim ad minim veniam, quis nostrud exercitation ullamco laboris nisi ut aliquip ex ea commodo consequat.</p>
    <span class="card-more">READ MORE <i></i></span>
  </article>
</header>

<section class="abs meter">
  <p class="meter-q">Are you working enterpreneurship-like?</p>
  <svg width="276" height="259" viewBox="23 507 276 259">
    <path d="M32,690 A123,123 0 0 1 55.5,617.7 L98.4,648.8 A70,70 0 0 0 85,690 Z" fill="#2f9a3b"/>
    <path d="M55.5,617.7 A123,123 0 0 1 117,573 L133.4,623.4 A70,70 0 0 0 98.4,648.8 Z" fill="#8dbf2a"/>
    <path d="M117,573 A123,123 0 0 1 193,573 L176.6,623.4 A70,70 0 0 0 133.4,623.4 Z" fill="#f6ac10"/>
    <path d="M193,573 A123,123 0 0 1 254.5,617.7 L211.6,648.8 A70,70 0 0 0 176.6,623.4 Z" fill="#ee6a1b"/>
    <path d="M254.5,617.7 A123,123 0 0 1 278,690 L225,690 A70,70 0 0 0 211.6,648.8 Z" fill="#cf1a2b"/>
    <g stroke="#fff" stroke-width="1" opacity=".6">
      <line x1="55.5" y1="617.7" x2="98.4" y2="648.8"/><line x1="117" y1="573" x2="133.4" y2="623.4"/>
      <line x1="193" y1="573" x2="176.6" y2="623.4"/><line x1="254.5" y1="617.7" x2="211.6" y2="648.8"/>
    </g>
    <g font-family="Arimo, sans-serif" font-size="22" fill="#fff" text-anchor="middle">
      <text x="60" y="674">1</text><text x="95" y="620">2</text><text x="155" y="598">3</text><text x="225" y="622">4</text><text x="256" y="674">5</text>
    </g>
    <line x1="155" y1="688" x2="155" y2="650" stroke="#111" stroke-width="4"/>
    <polygon points="155,636 145,656 165,656" fill="#111"/>
    <circle cx="155" cy="688" r="5" fill="#111"/>
  </svg>
  <p class="meter-check">CHECK YOUR LEVEL</p>
  <p class="meter-try">TRY THE LURVIKMETER</p>
</section>

<div class="abs bar bar-start"><i></i>GETTING STARTED</div>
<section class="abs start-box">
  <div class="col" style="left:21px">
    <h3>METHODS</h3>
    <ul><li>CAFE-PEDAGOGIKK</li><li>ELEVBEDRIFT</li><li>GRUNDERCAMP</li><li>STORY LINE</li><li>TOPP</li></ul>
  </div>
  <div class="divider" style="left:204px"></div>
  <div class="col" style="left:251px">
    <h3>TEACHING PLANS</h3>
    <ul><li>CAFE-PEDAGOGIKK</li><li>ELEVBEDRIFT</li><li>GRUNDERCAMP</li><li>STORY LINE</li><li>TOPP</li></ul>
  </div>
  <div class="divider" style="left:435px"></div>
  <div class="col" style="left:481px">
    <h3 class="plain">METHODS</h3>
    <ul><li>CAFE-PEDAGOGIKK</li><li>ELEVBEDRIFT</li><li>GRUNDERCAMP</li><li>STORY LINE</li><li>TOPP</li></ul>
  </div>
  <span class="pill-dark" style="left:93px">SEE MORE ⇢</span>
  <span class="pill-dark" style="left:323px">SEE MORE ⇢</span>
  <span class="pill-dark" style="left:553px">SEE MORE ⇢</span>
</section>

<div class="abs bar bar-inspire"><i></i>INSPIRATION</div>
<span class="abs slide-arrow" style="left:8px;border-right:11px solid #111"></span>
<span class="abs slide-arrow" style="left:980px;border-left:11px solid #111"></span>
<figure class="abs thumb" style="left:29px"><div class="photo photo-a" role="img" aria-label="Photo of a school building with a bare tree in front"></div><figcaption class="label">SMÅ-TOPP AT VASSBYGD SCHOOL</figcaption></figure>
<figure class="abs thumb" style="left:219px"><div class="photo photo-b" role="img" aria-label="Photo of a brick school sign with shrubs"></div><figcaption class="label">NORTH ALDERBY SCHOOL</figcaption></figure>
<figure class="abs thumb" style="left:409px"><div class="photo photo-a" role="img" aria-label="Photo of a school building with a bare tree in front"></div><figcaption class="label">SMÅ-TOPP AT VASSBYGD SCHOOL</figcaption></figure>
<figure class="abs thumb" style="left:599px"><div class="photo photo-c" role="img" aria-label="Photo of a modern school building under blue sky"></div><figcaption class="label">TOR HAVLAND SCHOOL</figcaption></figure>
<figure class="abs thumb" style="left:789px"><div class="photo photo-a" role="img" aria-label="Photo of a school building with a bare tree in front"></div><figcaption class="label">SMÅ-TOPP AT VASSBYGD SCHOOL</figcaption></figure>

<footer class="abs footer">
  <div class="fcol" style="left:25px">
    <h4>PEDAGOGICAL ENTREPRENEURSHIP</h4>
    <p>What is pedagogical<br>entrepreneurship?<br>Science<br>Best Practice Schools<br>Lurvikmeter<br>About Lurvik.no</p>
  </div>
  <span class="pill" style="left:23px;top:178px">SEE MORE ⇢</span>
  <div class="fcol" style="left:265px">
    <h4>METHODS</h4>
    <p>Story line<br>TOPP<br>Cafe-pedagogikk</p>
  </div>
  <span class="pill" style="left:263px;top:129px">SEE MORE ⇢</span>
  <div class="fcol" style="left:416px">
    <h4>TEACHING PLANS</h4>
    <p>Teaching Plan 1<br>Teaching Plan 2<br>Teaching Plan 3<br>Teaching Plan 4</p>
  </div>
  <span class="pill" style="left:416px;top:144px">SEE MORE ⇢</span>
  <div class="fcol" style="left:576px">
    <h4>GOOD EXAMPLES</h4>
    <p>Små-TOPP at Vassbygd School<br>Små-TOPP at Vassbygd School<br>Små-TOPP at Vassbygd School<br>Små-TOPP at Vassbygd School<br>Små-TOPP at Vassbygd School</p>
  </div>
  <span class="pill" style="left:576px;top:161px">SEE MORE ⇢</span>
  <div class="abs f-divider"></div>
  <span class="abs social" style="left:807px"></span>
  <span class="abs social" style="left:850px"></span>
  <span class="abs social" style="left:894px"></span>
  <span class="abs social" style="left:937px"></span>
  <span class="abs f-mark"></span>
  <p class="abs f-copy">Lurvik.no<br>Copyrights 2012.All Rights Reserved.</p>
</footer>

</body>
</html>
```